jQuery Mobile CSS for web app

Task Outline:
Create jQuery Mobile themeroller compliant CSS and icons for a mobile web app.
Task Description:
Brindle Solutions are in the process of implementing a new, web based version of their Tessel operations platform.
The web based version of Tessel is built on top of the jQuery Mobile platform and we are looking for a designer to create a jQuery Mobile themeroller compliant CSS theme pack that we can plug into our application. The aim is to remove the standard jQuery Mobile look and feel and to introduce the Brindle branding throughout the new web app.
A number of screenshots are shown in the attached design spec (brindle_solutions.pdf) that show what the current (Windows Mobile 6.5) application looks like, alongside the development version of our new web app.
Deliverables:
• jQuery Mobile (v 1.4.2) themeroller compliant CSS which provides theming for all jQuery Mobile UI components.
• Example html showing how to use the CSS theme (especially where additional html/css classes are required).
• New set of status icons (as listed in attachment)
Inspiration:
See our website for current branding: www.brindle-solutions-demo.net

```html
<!DOCTYPE html>
<html lang="en">
<head>
<meta charset="utf-8">
<title>Brindle Tessel – Ticket Menu</title>
<link rel="stylesheet" href="https://fonts.googleapis.com/css2?family=Mulish:wght@400;600;700;800&display=swap">
<style>
  :root {
    --status-bg: #111214;
    --status-text: #e8e8e8;
    --brand-red: #d9161c;
    --brand-red-dark: #b30d12;
    --brand-red-light: #ec3a36;
    --ticket-bg: #e9e9e9;
    --ticket-text: #555;
    --list-bg: #ffffff;
    --divider: #dcdcdc;
    --title-text: #333;
    --sub-text: #8a8a8a;
    --crew: #f7a21b;
    --crew-dark: #ee7a0d;
    --material: #d9161c;
    --material-dark: #a90f13;
    --inventory: #1f6fd8;
    --inventory-dark: #0d4fb0;
    --equipment: #8b2bbf;
    --equipment-dark: #5e1a90;
    --footer-bg: #f4f4f4;
    --footer-alt: #e6e6e6;
    --footer-text: #333;
  }
  * { box-sizing: border-box; margin: 0; padding: 0; }
  html, body { width: 855px; height: 1200px; overflow: hidden; }
  body {
    font-family: "Mulish", Arial, sans-serif;
    background: var(--list-bg);
  }
  .app {
    width: 855px; height: 1200px;
    display: flex; flex-direction: column;
  }
  .status-bar {
    height: 48px;
    background: var(--status-bg);
    color: var(--status-text);
    display: flex; align-items: center; justify-content: space-between;
    padding: 0 22px;
    font-size: 22px; font-weight: 600;
  }
  .status-left, .status-right { display: flex; align-items: center; gap: 10px; width: 160px; }
  .status-right { justify-content: flex-end; }
  .battery { width: 38px; height: 18px; border: 2px solid var(--status-text); border-radius: 3px; padding: 2px; }
  .battery span { display: block; width: 100%; height: 100%; background: #4cd964; }
  .app-header {
    height: 112px;
    background: linear-gradient(var(--brand-red-light), var(--brand-red) 55%, var(--brand-red-dark));
    color: #fff;
    display: flex; align-items: center; justify-content: center;
    font-size: 50px; font-weight: 700; letter-spacing: 0.5px;
  }
  .ticket-bar {
    height: 64px;
    background: var(--ticket-bg);
    border-bottom: 2px solid var(--divider);
    color: var(--ticket-text);
    display: flex; align-items: center; justify-content: center;
    font-size: 28px; font-weight: 600;
  }
  .menu-list { list-style: none; }
  .menu-item {
    height: 148px;
    display: flex; align-items: center;
    padding: 0 40px;
    border-bottom: 2px solid var(--divider);
    gap: 34px;
  }
  .menu-icon {
    width: 104px; height: 104px; border-radius: 14px;
    display: flex; align-items: center; justify-content: center;
    flex-shrink: 0;
  }
  .icon-crew { background: linear-gradient(var(--crew), var(--crew-dark)); }
  .icon-material { background: linear-gradient(var(--material), var(--material-dark)); }
  .icon-inventory { background: linear-gradient(var(--inventory), var(--inventory-dark)); }
  .icon-equipment { background: linear-gradient(var(--equipment), var(--equipment-dark)); }
  .menu-title { font-size: 38px; color: var(--title-text); white-space: nowrap; }
  .menu-sub { font-size: 24px; color: var(--sub-text); margin-top: 4px; }
  .spacer { flex: 1; background: var(--list-bg); }
  .nav-footer {
    height: 96px;
    display: flex;
    border-top: 2px solid var(--divider);
  }
  .nav-button {
    flex: 1;
    display: flex; align-items: center; justify-content: center; gap: 14px;
    font-size: 34px; color: var(--footer-text); font-weight: 600;
    background: var(--footer-bg);
  }
  .nav-button.next { background: var(--footer-alt); }
</style>
</head>
<body>
<main class="app">
  <div class="status-bar">
    <div class="status-left">
      <svg width="30" height="20" viewBox="0 0 30 20" aria-hidden="true">
        <rect x="0" y="14" width="4" height="6" fill="#e8e8e8"/>
        <rect x="7" y="10" width="4" height="10" fill="#e8e8e8"/>
        <rect x="14" y="6" width="4" height="14" fill="#e8e8e8"/>
        <rect x="21" y="2" width="4" height="18" fill="#e8e8e8"/>
      </svg>
      <span>3G</span>
    </div>
    <span class="status-time">8:33 PM</span>
    <div class="status-right">
      <span>98%</span>
      <div class="battery"><span></span></div>
    </div>
  </div>

  <header class="app-header">Brindle Tessel</header>
  <div class="ticket-bar">Ticket - 700065</div>

  <ul class="menu-list">
    <li class="menu-item">
      <div class="menu-icon icon-crew">
        <svg width="64" height="64" viewBox="0 0 64 64" aria-hidden="true">
          <circle cx="32" cy="22" r="12" fill="#fff"/>
          <path d="M10 58c0-14 10-22 22-22s22 8 22 22z" fill="#fff"/>
        </svg>
      </div>
      <div><div class="menu-title">Crew</div><div class="menu-sub">Etiam nunc venenatis n tristique</div></div>
    </li>
    <li class="menu-item">
      <div class="menu-icon icon-material">
        <svg width="64" height="64" viewBox="0 0 64 64" aria-hidden="true">
          <rect x="26" y="4" width="12" height="56" rx="2" fill="#fff" transform="rotate(45 32 32)"/>
          <rect x="27" y="6" width="10" height="46" fill="#fff" transform="rotate(-45 32 32)"/>
          <path d="M27 52h10l-5 9z" fill="#fff" transform="rotate(-45 32 32)"/>
        </svg>
      </div>
      <div><div class="menu-title">Material/Subcontractor</div><div class="menu-sub">Etiam nunc venenatis n tristique</div></div>
    </li>
    <li class="menu-item">
      <div class="menu-icon icon-inventory">
        <svg width="64" height="64" viewBox="0 0 64 64" aria-hidden="true">
          <path d="M14 12h36l8 20H6z" fill="#fff"/>
          <rect x="6" y="34" width="52" height="20" rx="2" fill="#fff"/>
          <rect x="24" y="40" width="16" height="4" fill="#1f6fd8"/>
        </svg>
      </div>
      <div><div class="menu-title">Inventory</div><div class="menu-sub">Etiam nunc venenatis n tristique</div></div>
    </li>
    <li class="menu-item">
      <div class="menu-icon icon-equipment">
        <svg width="64" height="64" viewBox="0 0 64 64" aria-hidden="true">
          <rect x="28" y="14" width="8" height="44" rx="3" fill="#fff" transform="rotate(-45 32 32)"/>
          <circle cx="15" cy="15" r="10" fill="#fff"/>
          <circle cx="11" cy="11" r="5" fill="#8b2bbf"/>
          <rect x="29" y="2" width="6" height="40" fill="#fff" transform="rotate(45 32 32)"/>
          <rect x="27" y="40" width="10" height="20" rx="3" fill="#fff" transform="rotate(45 32 32)"/>
        </svg>
      </div>
      <div><div class="menu-title">Equipment/Non-Labor R</div><div class="menu-sub">Etiam nunc venenatis n tristique</div></div>
    </li>
  </ul>

  <div class="spacer"></div>

  <nav class="nav-footer">
    <div class="nav-button back">
      <svg width="34" height="34" viewBox="0 0 34 34" aria-hidden="true">
        <circle cx="17" cy="17" r="15" fill="none" stroke="#333" stroke-width="3"/>
        <path d="M24 17H11M16 11l-6 6 6 6" fill="none" stroke="#333" stroke-width="3"/>
      </svg>
      Back
    </div>
    <div class="nav-button next">
      Next
      <svg width="34" height="34" viewBox="0 0 34 34" aria-hidden="true">
        <circle cx="17" cy="17" r="15" fill="none" stroke="#333" stroke-width="3"/>
        <path d="M10 17h13M18 11l6 6-6 6" fill="none" stroke="#333" stroke-width="3"/>
      </svg>
    </div>
  </nav>
</main>
</body>
</html>
```